Need website for Dating "Game" App

I need a one or two page website for a new dating "game" app (patent pending) called wooSpark.net. The game will be "interactive" and is designed to be a fun, safe and nonthreatening way to help two people get to know more about each other "before making a face to face date". The App will be configured somewhat like a dating app/website where members browse profiles to find someone they are interested in getting to know.
I am looking for a design that will capture the attention of singles who are tired of wasting time on face to face dates with individuals they are not compatible with. This website will be used as somewhat of a launch page for a Fundlaunch campaign because the app is still in the development stage.

Target Market(s)

Single daters who are looking for a compatible mate

Industry/Entity Type

Dating

Number of Pages Required

2 page

Requirements
Must have
• Mention that the game is Patent Pending
• Must be whimsical but with a classy-clean look (the game is designed to be fun)
• I have a 30 second video completed that I would like incorporated on the website.
• Logo colors must stay the same
• Page must direct to my upcoming Fundlaunch campaign - (Dating App is still in development stage)
Nice to have
• 1. The game will populate relationship/lifestyle like questions to two players who opt to play the game together. The design could possibly have some fun relationship questions "raining" down on the page.
• 2. Tag line...MEET - PLAY - DATE (T.M.)
• Meet - Browse profiles to find someone whom you want to get to know better and invite them to play!
• Play - Many dating sites take you through a grueling set of questions before you upload a profile. You are then matched with individuals that an "algorithm" determines you are most compatible with. The problem with this method is that only the algorithm knows what areas you and those individuals have in common. WooSpark.net alleviates the guesswork by placing the power of the algorithm in your hands with a fun, safe and nonthreatening game that helps you get to know your person of interest before meeting face to face!
• Date -
• 3. "Wouldn't it be great to get to know someone better before making a date?"
Should not have
• Nothing raunchy.
• I don't want the basic 'dating website' look (although I do like the "Tulip Finds Lantern" site.

```html
<!DOCTYPE html>
<html lang="en">
<head>
<meta charset="utf-8">
<title>wooSpark.net — Meet, Play, Date</title>
<link rel="stylesheet" href="https://fonts.googleapis.com/css2?family=Lato:wght@300;400;700;900&display=swap">
<style>
:root{
  --red:#e3262b;
  --red-soft:#f4b8ba;
  --ink:#1d1d1d;
  --text:#555;
  --muted:#8a8a8a;
  --line:#d9d9d9;
  --bg-soft:#f6f6f6;
  --white:#fff;
  --footer:#2b2b2b;
}
*{box-sizing:border-box;margin:0;padding:0}
html,body{width:1200px;height:3267px;overflow:hidden}
body{position:relative;font-family:'Lato',Arial,sans-serif;color:var(--text);background:var(--bg-soft)}
.abs{position:absolute}
.accent{color:var(--red)}

/* hero */
.hero{left:0;top:0;width:1200px;height:606px;background:radial-gradient(ellipse at 58% 30%,#8a8683 0%,#5b5755 45%,#3a3735 100%)}
.hero-photo{left:0;top:0;width:1200px;height:606px;background:linear-gradient(115deg,rgba(220,215,210,.18) 0%,rgba(0,0,0,0) 40%,rgba(255,255,255,.12) 80%)}
.brand{left:113px;top:96px;display:flex;align-items:center;gap:10px}
.brand-dot{width:16px;height:16px;border-radius:50%;background:var(--red)}
.brand-name{font-size:34px;font-weight:700;color:var(--red);letter-spacing:-.5px}
.brand-tag{left:146px;top:144px;font-size:15px;color:var(--white);font-weight:700}
.menu-btn{left:1084px;top:50px;width:34px;height:24px;border:2px solid #ddd;border-radius:3px;display:flex;flex-direction:column;justify-content:center;gap:3px;padding:0 6px}
.menu-btn span{height:2px;background:#ddd}
.store-btn{top:447px;height:58px;background:#000;border:2px solid #a6a6a6;border-radius:8px;color:#fff;display:flex;flex-direction:column;justify-content:center;padding-left:26px}
.store-btn small{font-size:11px;letter-spacing:.5px}
.store-btn b{font-size:25px;font-weight:400;line-height:1}

/* section heading */
.heading{width:1200px;left:0;text-align:center;font-size:31px;font-weight:400;color:var(--ink)}
.rule{left:435px;width:330px;height:2px;background:var(--line)}
.rule::before{content:"";position:absolute;left:0;top:0;width:48px;height:2px;background:var(--red)}

/* steps */
.intro{left:96px;top:738px;width:1008px;font-size:13px;line-height:25px;text-align:center}
.phone{top:828px;width:152px;height:326px;border-radius:22px;background:#ececec;border:1px solid #e2e2e2}
.phone.active{background:#1a1a1a;border-color:#000;box-shadow:0 6px 14px rgba(0,0,0,.25)}
.screen{position:absolute;left:10px;top:40px;width:132px;height:240px;background:var(--red-soft);opacity:.85;color:#fff;text-align:center;font-size:11px;line-height:15px;padding:0 10px}
.phone.active .screen{background:var(--red);opacity:1}
.screen h4{font-size:17px;font-weight:700;background:rgba(0,0,0,.12);margin:0 -10px 12px;padding:8px 0}
.home-key{position:absolute;left:63px;bottom:10px;width:24px;height:24px;border-radius:50%;border:2px solid #d5d5d5}
.phone.active .home-key{border-color:#555}
.screen-brand{margin-top:86px;font-size:14px;font-weight:700}
.screen-cta{margin:34px auto 0;width:96px;padding:5px 0;border:1px solid #fff;font-size:10px}
.screen-photo{display:block;margin:0 -2px;height:150px;background:linear-gradient(135deg,#d9a070,#a86a4a 60%,#e6c190)}
.slider{left:187px;top:1201px;width:826px;height:5px;background:var(--red);border-radius:3px}
.knob{left:483px;top:1194px;width:19px;height:19px;border-radius:50%;background:#eee;border:2px solid #bbb}
.step-no{top:1224px;width:60px;font-size:21px;text-align:center;color:#777}
.step-no.active{color:var(--red)}

/* featured */
.band{left:0;top:1302px;width:1200px;height:194px;background:linear-gradient(180deg,#e7e3e5,#f1eef0)}
.video{left:98px;top:1376px;width:536px;height:427px;background:radial-gradient(circle at 55% 40%,#c0282c 0%,#5a1d1e 40%,#1b1515 80%)}
.play{left:326px;top:1559px;width:86px;height:86px;border-radius:50%;background:#fff}
.play::after{content:"";position:absolute;left:33px;top:26px;border-left:26px solid #111;border-top:17px solid transparent;border-bottom:17px solid transparent}
.video-card{left:584px;top:1448px;width:518px;height:327px;background:#f0f0f0;border:1px solid #e2e2e2;box-shadow:0 2px 6px rgba(0,0,0,.12);padding:46px 36px}
.video-card h2{font-size:30px;font-weight:400;color:var(--ink)}
.video-card .rule{position:relative;left:0;width:48px;margin:20px 0 22px}
.video-card p{font-size:13px;line-height:25px}

/* stories */
.card{top:2032px;width:331px;height:423px;background:#fff;box-shadow:0 1px 3px rgba(0,0,0,.06)}
.card-photo{height:196px;background:linear-gradient(135deg,#c8b6a2,#8e7a68 55%,#d8d2c8)}
.card h3{font-size:15px;font-weight:700;color:#333;padding:16px 16px 14px;border-bottom:1px solid #eee}
.card p{font-size:12.5px;line-height:21px;padding:14px 16px;height:128px}
.share{display:flex;border-top:1px solid #eee;height:36px;align-items:center;font-size:12px}
.share span:first-child{flex:1;padding-left:16px;border-right:1px solid #eee;height:100%;line-height:36px}
.share .net{width:40px;text-align:center;border-right:1px solid #eee;height:100%;line-height:36px;font-size:10px;color:#444}
.dots{left:566px;top:2502px;display:flex;gap:9px}
.dots i{width:7px;height:7px;border-radius:50%;background:#666}
.dots i.on{background:var(--red)}

/* about */
.about{left:0;top:2566px;width:1200px;height:396px;background:#fff}
.about-text{left:83px;top:2706px;width:680px;font-size:13.5px;line-height:28.5px}
.about-photo{left:871px;top:2668px;width:244px;height:262px;background:radial-gradient(ellipse at 50% 45%,#e8c8b2 0%,#f6ece6 55%,#fff 80%)}

/* contact */
.contact-text{left:0;top:3098px;width:1200px;text-align:center;font-size:14px;color:#333}
.social{top:3160px;font-size:14px;color:#444;font-weight:700}

.footer{left:0;top:3224px;width:1200px;height:43px;background:var(--footer);color:#ddd;font-size:12px;display:flex;align-items:center;justify-content:space-between;padding:0 84px}
</style>
</head>
<body>

<section class="abs hero" role="img" aria-label="Photo of hands holding a smartphone showing the app, blurred coffee cup in the background"></section>
<div class="abs hero-photo"></div>
<div class="abs brand"><span class="brand-dot"></span><span class="brand-name">wooSpark.net</span></div>
<div class="abs brand-tag">don't do dating without it</div>
<div class="abs menu-btn"><span></span><span></span><span></span></div>
<a class="abs store-btn" style="left:401px;width:200px"><small>GET IT ON</small><b>Play Bazaar</b></a>
<a class="abs store-btn" style="left:621px;width:179px"><small>GET IT ON</small><b>App Harbor</b></a>

<h2 class="abs heading" style="top:648px">Step to Find <span class="accent">Your Match</span></h2>
<div class="abs rule" style="top:707px"></div>
<p class="abs intro">Lorem ipsum dolor sit amet, consectetuer adipiscing elit, sed diam nonummy nibh euismod tincidunt ut laoreet dolore magna aliquam erat volutpat. Ut wisi enim ad minim veniam, quis nostrud exerci tation ullamcorper suscipit lobortis nisl ut aliquip ex ea commodo consequat.</p>

<div class="abs phone" style="left:203px"><div class="screen"><div class="screen-brand">wooSpark.net</div><div class="screen-cta">Create Account</div></div><span class="home-key"></span></div>
<div class="abs phone active" style="left:414px"><div class="screen"><h4>Meet</h4>Browse profiles to find someone whom you want to get to know better and invite them to play!</div><span class="home-key"></span></div>
<div class="abs phone" style="left:627px"><div class="screen"><h4>Play</h4>Many dating sites take you through a grueling set of questions before you upload a profile. You are then matched with individuals that an "algorithm" determines you are</div><span class="home-key"></span></div>
<div class="abs phone" style="left:841px"><div class="screen"><h4>Date</h4><span class="screen-photo" role="img" aria-label="Photo of a smiling couple on a date"></span></div><span class="home-key"></span></div>

<div class="abs slider"></div>
<div class="abs knob"></div>
<div class="abs step-no" style="left:249px">01</div>
<div class="abs step-no active" style="left:462px">02</div>
<div class="abs step-no" style="left:678px">03</div>
<div class="abs step-no" style="left:896px">04</div>

<div class="abs band" role="img" aria-label="Soft photo of pink and white paper heart garlands"></div>
<div class="abs video" role="img" aria-label="Video still: hands holding a phone with red hearts floating above it"></div>
<div class="abs play"></div>
<div class="abs video-card">
  <h2>Featured <span class="accent">Video</span></h2>
  <div class="rule"></div>
  <p>Lorem ipsum dolor sit amet, consectetuer adipiscing elit, sed diam nonummy nibh euismod tincidunt ut laoreet dolore magna aliquam erat volutpat. Ut wisi enim ad minim veniam, quis nostrud exerci tation ullamcorper suscipit lobortis nisl ut aliquip ex ea commodo consequat. Duis autem vel eum iriure dolor in hendrerit in vulputate ve</p>
</div>

<h2 class="abs heading" style="top:1898px">Success <span class="accent">Stories</span></h2>
<div class="abs rule" style="top:1955px"></div>

<article class="abs card" style="left:81px"><div class="card-photo" role="img" aria-label="Photo of a couple sharing wine at an outdoor table"></div><h3>Partner of the Month</h3><p>Lorem ipsum dolor sit amet, consectetuer adipiscing elit, sed diam nonummy nibh euismod tincidunt ut laoreet dolore magna aliquam erat volutpat. Ut wisi enim ad minim veniam...</p><div class="share"><span>Share on</span><span class="net">Wall</span><span class="net">Chirp</span><span class="net">Link</span><span class="net">Circ</span></div></article>
<article class="abs card" style="left:436px"><div class="card-photo" role="img" aria-label="Photo of a couple laughing in a cafe"></div><h3>Partner of the Month</h3><p>Lorem ipsum dolor sit amet, consectetuer adipiscing elit, sed diam nonummy nibh euismod tincidunt ut laoreet dolore magna aliquam erat volutpat. Ut wisi enim ad minim veniam...</p><div class="share"><span>Share on</span><span class="net">Wall</span><span class="net">Chirp</span><span class="net">Link</span><span class="net">Circ</span></div></article>
<article class="abs card" style="left:788px"><div class="card-photo" role="img" aria-label="Photo of a smiling couple at a street cafe"></div><h3>Partner of the Month</h3><p>Lorem ipsum dolor sit amet, consectetuer adipiscing elit, sed diam nonummy nibh euismod tincidunt ut laoreet dolore magna aliquam erat volutpat. Ut wisi enim ad minim veniam...</p><div class="share"><span>Share on</span><span class="net">Wall</span><span class="net">Chirp</span><span class="net">Link</span><span class="net">Circ</span></div></article>

<div class="abs dots"><i></i><i class="on"></i><i></i><i></i></div>

<section class="abs about"></section>
<h2 class="abs heading" style="top:2599px">About <span class="accent">wooSpark</span></h2>
<div class="abs rule" style="top:2660px"></div>
<p class="abs about-text">Lorem ipsum dolor sit amet, consectetuer adipiscing elit, sed diam nonummy nibh euismod ut laoreet dolore magna aliquam erat volutpat. Ut wisi enim ad minim veniam, quis nostrud exerci tation ullamcorper suscipit lobortis nisl aliquip ex ea commodo consequat. Duis autem vel eum iriure dolor in hendrerit in vulputate velit esse molestie consequat, vel illum dolore eu feugiat nulla facilisis at vero eros et accumsan iusto odio dignissim qui blandit praesent luptatum zzril delenit augue duis dolore te feugait odio dignissim qui blandit autem vel eum iriure dolor in hendrerit in vulputate velit esse molestie consequat facilisi.</p>
<div class="abs about-photo" role="img" aria-label="Photo of a smiling woman lying down looking at her phone"></div>

<h2 class="abs heading" style="top:3006px">Contact <span class="accent">Us</span></h2>
<div class="abs rule" style="top:3067px"></div>
<p class="abs contact-text">Questions for us? Technical issues, suggestions, or other inquiries? <span class="accent">Contact us!</span></p>
<span class="abs social" style="left:488px">Wall</span>
<span class="abs social" style="left:566px">Chirp</span>
<span class="abs social" style="left:650px">Circles+</span>

<footer class="abs footer"><span>Copyright 2016 wooSpark.net &nbsp;|&nbsp; All Rights Reserved</span><span>Privacy &amp; Terms</span></footer>

</body>
</html>
```